Meadowrun Acres Website Design

We have been redeveloping our website already and are quite happy with the content, but the design needs to be better:
https://tilvexa-hub.examplehost.net/

Pages, content, concept etc. Can all be taken from the redeveloped website.
The farmer can register and edit/view their profile, subscribe and these pages need to be designed better as well as contact, about, pricing, tos, privacy and a page with example portlets.

We need a website to appeal to farmers, investors and retiring farmers.

The design should be clean and a little country.

We don't want any repeat designs that some may submit to every project and has no respect for the project brief, so please don't submit them.

Target Market(s)

farmers, investors, retirees

Industry/Entity Type

Farming

Number of Pages Required

5+ page

Colors

Designer to choose colors to be used in the design.

Requirements
Must have
• Nice, clean modern design that is appealing
• Profile page laid out nicely

```html
<!DOCTYPE html>
<html lang="en">
<head>
<meta charset="utf-8">
<title>Meadowrun Acres – Pages</title>
<link href="https://fonts.googleapis.com/css2?family=Arimo:wght@400;700&display=swap" rel="stylesheet">
<style>
:root{
  --green:#2fa838;
  --green-dark:#23902c;
  --ink:#1a1a1a;
  --muted:#888;
  --line:#c9c9c9;
  --tile:#efefef;
  --tile-active:#cacaca;
  --red:#e0462f;
  --red-dark:#c73a25;
  --blue:#2c4899;
  --blue-dark:#243c84;
  --grey-btn:#a9a9a9;
}
*{box-sizing:border-box;margin:0;padding:0}
html,body{width:1200px;height:1169px;overflow:hidden;background:#fff}
body{font-family:"Arimo",Arial,sans-serif;color:var(--ink)}
.board{position:absolute;left:0;top:0;width:1500px;height:1461px;transform:scale(.8);transform-origin:0 0;overflow:hidden}
.abs{position:absolute}
.page{position:absolute;overflow:hidden}

/* header */
.socials{position:absolute;display:flex;align-items:center;gap:7px}
.dot{width:12px;height:12px;border-radius:50%;background:var(--green)}
.pill{border-radius:12px;font-size:12px;line-height:1;padding:4px 9px;white-space:nowrap}
.pill.solid{background:var(--green);color:#fff}
.pill.outline{border:1.5px solid var(--green);color:var(--green);background:#fff}
.brand{position:absolute;display:flex;align-items:center;gap:10px;font-size:18px;white-space:nowrap}
.brand .mark{width:14px;height:14px;border-radius:50%;border:2px solid var(--green)}
.nav{position:absolute;right:22px;display:flex;gap:13px;font-size:11px;list-style:none;align-items:center;white-space:nowrap}
.nav .pill{font-size:12px;padding:5px 12px}

/* type */
.title{position:absolute;color:var(--green);font-weight:700;text-align:center;white-space:nowrap;transform:translateX(-50%)}
.label{position:absolute;font-weight:700;font-size:14px;text-align:center;white-space:nowrap;transform:translateX(-50%)}
.field-label{position:absolute;font-weight:700;font-size:12px;text-align:right;white-space:nowrap;transform:translateX(-100%)}
.input{position:absolute;border:1px solid var(--line);background:#fff}
.panel{position:absolute;border:1.5px solid #d3d3d3;background:#fff}

/* buttons */
.social-btn{position:absolute;display:flex;align-items:center;color:#fff;font-size:17px;border-radius:3px;white-space:nowrap;overflow:hidden}
.social-btn .icon{width:44px;flex:none;height:100%;display:flex;align-items:center;justify-content:center}
.social-btn .icon span{width:14px;height:14px;background:#fff;opacity:.85}
.social-btn.red{background:var(--red)}
.social-btn.red .icon{background:var(--red-dark)}
.social-btn.blue{background:var(--blue)}
.social-btn.blue .icon{background:var(--blue-dark)}
.social-btn .txt{flex:1;text-align:center}
.cta{position:absolute;background:var(--green);color:#fff;font-size:21px;border-radius:24px;display:flex;align-items:center;justify-content:center;border:2px solid var(--green-dark);white-space:nowrap}

/* tiles */
.tile{position:absolute;width:130px;height:95px;background:var(--tile);text-align:center;color:var(--green);font-size:8px;font-weight:700}
.tile.active{background:var(--tile-active)}
.tile .art{width:40px;height:44px;margin:10px auto 12px;border-radius:6px}
.plan{position:absolute;display:flex;align-items:center;gap:18px;font-size:8px;font-weight:700;color:var(--green);white-space:nowrap}
.plan .opt{display:flex;align-items:center;gap:8px}
.box{width:11px;height:11px;border:1px solid #999;font-size:9px;color:#333;display:flex;align-items:center;justify-content:center}

/* footer */
.footer{position:absolute;font-size:13px;color:#555;white-space:nowrap}
.support{position:absolute;right:18px;display:flex;align-items:center;gap:7px;font-size:12.5px;color:#555;white-space:nowrap}
.support b{color:var(--green)}
.support .pill{font-size:11px}

/* contact */
.small{position:absolute;font-size:11px;white-space:nowrap}
.heading{position:absolute;color:var(--green);font-weight:700;font-size:18px;white-space:nowrap}
</style>
</head>
<body>
<div class="board">

  <!-- Registration page -->
  <section class="page" style="left:0;top:0;width:750px;height:1140px">
    <div class="socials" style="left:316px;top:17px"><i class="dot"></i><i class="dot"></i><i class="dot"></i><span class="pill solid">Donate</span></div>
    <div class="brand" style="left:22px;top:50px"><i class="mark"></i>Meadowrun Acres</div>
    <ul class="nav" style="top:52px"><li>Home</li><li>Aspiring Farmers</li><li>Farming Investors</li><li>Retiring Farmers</li><li>Our Blog</li><li>Pricing</li><li class="pill outline">Login</li></ul>

    <h1 class="title" style="left:372px;top:108px;font-size:40px">WELCOME TO THE FAMILY</h1>
    <div class="panel" style="left:144px;top:158px;width:457px;height:928px"></div>
    <h2 class="title" style="left:372px;top:189px;font-size:23px">REGISTRATION FORM</h2>
    <div class="label" style="left:372px;top:242px;font-size:13px">WHAT ARE YOU REGSTERING AS:</div>

    <div class="tile active" style="left:168px;top:282px"><div class="art" role="img" aria-label="Illustration of green rubber boots" style="background:#2f9a37"></div>REGISTER<br>as a Farmer</div>
    <div class="tile" style="left:307px;top:282px"><div class="art" role="img" aria-label="Illustration of a watering can" style="background:#3cb544"></div>REGISTER<br>as an Investor</div>
    <div class="tile" style="left:446px;top:282px"><div class="art" role="img" aria-label="Illustration of wheat stalks" style="background:#d8c49a"></div>REGISTER<br>as a Retiring Farmer</div>

    <div class="plan" style="left:203px;top:390px">
      <span class="opt"><i class="box"></i>Sarter (Free)</span>
      <span class="opt"><i class="box">x</i>Aspiring Farmer ($ 150/year)</span>
      <span class="opt"><i class="box"></i>Farm Ready ($ 400/year)</span>
    </div>

    <div class="label" style="left:372px;top:435px">SOCIAL MEDIA REGISTRATION</div>
    <div class="social-btn red" style="left:249px;top:473px;width:247px;height:45px"><div class="icon"><span></span></div><div class="txt">Sign up with Searchly</div></div>
    <div class="social-btn blue" style="left:249px;top:528px;width:247px;height:45px"><div class="icon"><span></span></div><div class="txt">Sign up with Friendbook</div></div>

    <div class="label" style="left:372px;top:607px">EMAIL REGISTRATION</div>

    <div class="field-label" style="left:296px;top:652px">FIRST NAME:</div><div class="input" style="left:305px;top:645px;width:219px;height:28px"></div>
    <div class="field-label" style="left:296px;top:685px">LAST NAME:</div><div class="input" style="left:305px;top:679px;width:219px;height:28px"></div>
    <div class="field-label" style="left:296px;top:720px">EMAIL:</div><div class="input" style="left:305px;top:713px;width:219px;height:28px"></div>
    <div class="field-label" style="left:296px;top:754px">PHONE NUMBER:</div><div class="input" style="left:305px;top:747px;width:219px;height:28px"></div>
    <div class="field-label" style="left:296px;top:806px">ADDRESS:</div><div class="input" style="left:305px;top:799px;width:219px;height:28px"></div>
    <div class="field-label" style="left:296px;top:841px">STATE:</div><div class="input" style="left:305px;top:834px;width:219px;height:28px"></div>
    <div class="field-label" style="left:296px;top:875px">CITY:</div><div class="input" style="left:305px;top:868px;width:219px;height:28px"></div>
    <div class="field-label" style="left:296px;top:910px">ZIPCODE:</div><div class="input" style="left:305px;top:903px;width:219px;height:28px"></div>
    <div class="field-label" style="left:296px;top:962px">PASSWORD:</div><div class="input" style="left:305px;top:955px;width:219px;height:28px"></div>
    <div class="field-label" style="left:296px;top:997px">RETYPE PASSWORD:</div><div class="input" style="left:305px;top:990px;width:219px;height:28px"></div>

    <div class="cta" style="left:280px;top:1042px;width:185px;height:48px">Sign Up Now &gt;</div>

    <div class="footer" style="left:16px;top:1105px">© Meadowrun Acres 2017</div>
    <div class="support" style="top:1101px"><span><b>Support:</b> Contact</span>|<span>Terms of Service</span>|<span>Privacy</span>|<span>Newsletter</span><span style="width:8px"></span><i class="dot"></i><i class="dot"></i><i class="dot"></i><span class="pill outline">Donate</span></div>
  </section>

  <!-- Login page -->
  <section class="page" style="left:756px;top:3px;width:744px;height:800px">
    <div class="socials" style="left:316px;top:17px"><i class="dot"></i><i class="dot"></i><i class="dot"></i><span class="pill solid">Donate</span></div>
    <div class="brand" style="left:22px;top:50px"><i class="mark"></i>Meadowrun Acres</div>
    <ul class="nav" style="top:52px"><li>Home</li><li>Aspiring Farmers</li><li>Farming Investors</li><li>Retiring Farmers</li><li>Our Blog</li><li>Pricing</li><li class="pill outline">Login</li></ul>

    <div class="abs" role="img" aria-label="Photo of a farmer on horseback in a green paddock with cattle and hills" style="left:0;top:87px;width:744px;height:352px;background:linear-gradient(180deg,#9fb0b3 0%,#6f7d52 35%,#7d8a4c 70%,#8a8656 100%)"></div>

    <div class="panel" style="left:176px;top:162px;width:393px;height:570px"></div>
    <h1 class="title" style="left:372px;top:185px;font-size:44px">LOGIN CENTER</h1>
    <div class="label" style="left:372px;top:256px;font-size:18px">SOCIAL LOGIN</div>
    <div class="social-btn red" style="left:248px;top:299px;width:248px;height:47px"><div class="icon"><span></span></div><div class="txt">Login with Searchly</div></div>
    <div class="social-btn blue" style="left:248px;top:357px;width:248px;height:47px"><div class="icon"><span></span></div><div class="txt">Login with Friendbook</div></div>

    <div class="label" style="left:372px;top:439px;font-size:18px">MEMBER LOGIN</div>
    <div class="field-label" style="left:295px;top:487px">EMAIL:</div><div class="input" style="left:305px;top:480px;width:219px;height:29px"></div>
    <div class="field-label" style="left:295px;top:521px">PASSWORD:</div><div class="input" style="left:305px;top:515px;width:219px;height:29px"></div>
    <div class="abs pill" style="left:305px;top:552px;background:var(--grey-btn);color:#fff;padding:4px 12px;font-size:11px">Login</div>
    <div class="abs" style="left:395px;top:549px;font-size:12px;color:var(--green);text-decoration:underline;white-space:nowrap">Forgot your password?</div>

    <div class="label" style="left:372px;top:607px;font-size:18px">DON’T HAVE AN ACCOUNT?</div>
    <div class="cta" style="left:280px;top:652px;width:185px;height:49px">Sign Up Now &gt;</div>

    <div class="footer" style="left:16px;top:774px">© Meadowrun Acres 2017</div>
    <div class="support" style="top:770px"><span><b>Support:</b> Contact</span>|<span>Terms of Service</span>|<span>Privacy</span>|<span>Newsletter</span><span style="width:8px"></span><i class="dot"></i><i class="dot"></i><i class="dot"></i><span class="pill outline">Donate</span></div>
  </section>

  <!-- Contact page -->
  <section class="page" style="left:756px;top:801px;width:744px;height:660px">
    <div class="socials" style="left:316px;top:17px"><i class="dot"></i><i class="dot"></i><i class="dot"></i><span class="pill solid">Donate</span></div>
    <div class="brand" style="left:20px;top:51px"><i class="mark"></i>Meadowrun Acres</div>
    <ul class="nav" style="top:52px"><li>Home</li><li>Aspiring Farmers</li><li>Farming Investors</li><li>Retiring Farmers</li><li>Our Blog</li><li>Pricing</li><li class="pill outline">Login</li></ul>

    <h1 class="title" style="left:376px;top:110px;font-size:42px">CONTACT US</h1>
    <div class="small" style="left:376px;top:159px;transform:translateX(-50%);color:var(--muted);text-align:center;line-height:13px">Please get in touch if you have any questions or suggestions.<br>We really do want to hear from you.</div>

    <div class="heading" style="left:143px;top:200px">EMAIL US:</div>
    <div class="heading" style="left:420px;top:200px">MEADOWRUN ACRES:</div>

    <div class="small" style="left:143px;top:235px">Your Full Name:</div><div class="input" style="left:141px;top:253px;width:252px;height:22px"></div>
    <div class="small" style="left:143px;top:280px">Your Email Address:</div><div class="input" style="left:141px;top:298px;width:252px;height:22px"></div>
    <div class="small" style="left:143px;top:326px">Your Phone Number:</div><div class="input" style="left:141px;top:344px;width:252px;height:22px"></div>
    <div class="small" style="left:143px;top:371px">Subject:</div><div class="input" style="left:141px;top:388px;width:252px;height:22px"></div>
    <div class="small" style="left:143px;top:415px">Message:</div><div class="input" style="left:141px;top:432px;width:252px;height:85px"></div>
    <div class="abs" style="left:340px;top:527px;width:53px;height:20px;background:#cfcfcf;color:#fff;font-size:11px;font-weight:700;display:flex;align-items:center;justify-content:center">Send</div>

    <div class="small" style="left:420px;top:235px"><b>#:</b> 0491 570 118</div>
    <div class="small" style="left:420px;top:255px"><b>@:</b> hello@meadowrunacres.net</div>
    <div class="small" style="left:420px;top:276px;line-height:13px">58 Brookfield Lane, Town<br>State, Australia, 2030</div>
    <div class="abs" role="img" aria-label="Map of Australia and the surrounding region" style="left:420px;top:319px;width:206px;height:282px;background:linear-gradient(160deg,#a8c8f0 0%,#b6d3f5 55%,#a9c9ef 100%)"></div>

    <div class="footer" style="left:12px;top:627px">© Meadowrun Acres 2017</div>
    <div class="support" style="top:623px"><span><b>Support:</b> Contact</span>|<span>Terms of Service</span>|<span>Privacy</span>|<span>Newsletter</span><span style="width:8px"></span><i class="dot"></i><i class="dot"></i><i class="dot"></i><span class="pill outline">Donate</span></div>
  </section>

</div>
</body>
</html>
```